Creative Web Design for an ERP (technology) Consulting Business

I need two pages designed for the ERP Project Management Consulting Company I am starting. One page is the home page, the other page is an important inside page.

I've looked at many different templates for sites like this, and they all look the same to me. I am working with PixelGuild designers because I want something unique.

This site will be implemented with Wordpress using the Elementor framework,

About Me ---
I have worked with PixelGuild several times before, and I have tired to do everything I can to ve helpful. In the uploads, you will find PDF's with wireframes outlning the layout of the pages, as well as explanatios for each section. There are Word documents that you can copy into text. The list below explains the files included.

Although the wireframes suggest a layout, please feel free to use your creativity - often, I find that the designs I like the most are designs I have never thought of.

About the Company --
ERP (Enterprise Resource Planning) systems are business computer systems that tie different businesss functions together. These systems are expensive and complicated, and efforts to implement them often fail. The purpose of the company is to increase the chance of success by focusing on the things that need to be right.

I have uploaded several files to help clarify what I am looking for:
• 1a - Home Page Wireframe - PDF
Wireframe for the home page with an explanation of each section.
• 1b - Home Page Text – Word
A Word document so that you can copy the text.
• 2 - Copper Harbor Logo – ZIP
Four different versions of the company logo in Adobe Illustrator, PNG, and JPG formats. Any of the four are acceptable:
1. Logo_1 – Black on Transparent – Same Line ERP
2. Logo_2 – White on Transparent – Same Line ERP
3. Logo_3 – Black on Transparent – Big ERP on Different Line
4. Logo_4 – White on Transparent – Big ERP on Different Line
• 3a - Copper Harbor Page Wireframe – PDF
Wireframe for he Copper Harbor page, with explanations and a detailed breakdown of the top section.
• 3b - Copper Harbor Text – Word
• 4 - Colors and Palettes – PDF
• 5 - Change Management Icon – EPS
• 6 – Site Map
If you wish to see it, the site map provides an idea of the entire site. The two pages circled in red are the ones I need to be designed.

Thank you for your interest in this project!

Target Market(s)

Corporate decision makers, primarily CIOs and CFOs, as well as ERP project managers and influencers.

Industry/Entity Type

Consulting

Number of Pages Required

2 page

Font styles to use
Sans Serif

Requirements
Must have
• Pages that contain the elements explained on the wireframes provided.
Nice to have
• A design that looks and feels unique
Should not have
• A typical, template layour

```html
<!DOCTYPE html>
<html lang="en">
<head>
<meta charset="utf-8">
<title>Norvale – Adaptive 8 Method</title>
<link href="https://fonts.googleapis.com/css2?family=Inter:wght@400;500;600;700&display=swap" rel="stylesheet">
<style>
:root{
  --ink:#14181f;
  --navy:#1f4365;
  --blue:#1d4f8a;
  --text:#2c3440;
  --muted:#5b6572;
  --orange:#f29a66;
  --orange-deep:#e7783f;
  --line:#e2e6ec;
  --soft:#eef1f6;
  --card:#ffffff;
  --star:#f2b84b;
  --dark:#232a33;
}
*{box-sizing:border-box;margin:0;padding:0}
html,body{width:673px;height:1200px;overflow:hidden;background:#fff}
body{font-family:"Inter",sans-serif;color:var(--text);position:relative}
.abs{position:absolute}

/* header */
.brand{left:16px;top:14px;display:flex;align-items:center;gap:6px;font-weight:700;font-size:17px;color:var(--ink)}
.brand-dot{width:12px;height:12px;border-radius:50%;background:var(--ink)}
.nav{top:22px;left:362px;display:flex;gap:16px;font-size:7.5px;font-weight:600;letter-spacing:.2px;color:var(--ink);text-transform:uppercase;white-space:nowrap}
.nav-cta{left:570px;top:10px;width:89px;height:31px;border-radius:16px;background:var(--dark);color:#fff;font-size:7.5px;font-weight:600;letter-spacing:.4px;display:flex;align-items:center;justify-content:center;text-transform:uppercase}

/* hero */
.eyebrow{left:16px;top:80px;color:var(--orange-deep);font-size:12px;font-weight:500}
.hero-title{left:16px;top:101px;font-size:25px;line-height:31px;font-weight:600;color:var(--ink);letter-spacing:-.3px}
.hero-copy{left:16px;top:179px;width:240px;font-size:9.6px;line-height:13.6px;color:var(--text)}
.hero-btn{left:15px;top:264px;width:146px;height:34px;border-radius:17px;background:var(--orange);display:flex;align-items:center;gap:10px;padding-left:13px;font-size:8px;font-weight:600;color:var(--ink);text-transform:uppercase}
.hero-btn .ico{width:14px;height:14px;border-radius:50%;background:var(--ink)}
.video{left:301px;top:91px;width:357px;height:209px;border-radius:12px;overflow:hidden;background:linear-gradient(90deg,#1c2026 0%,#2b3038 45%,#8a9099 70%,#b4b9c0 100%)}
.video-label{left:12px;top:10px;display:flex;align-items:center;gap:8px;color:#fff;font-size:8px}
.video-label span.c{width:14px;height:14px;border-radius:50%;border:1.5px solid #fff}
.video-bar{left:12px;bottom:10px;width:333px;height:40px}

/* testimonials */
.section-title{left:16px;top:364px;font-size:19px;font-weight:600;color:var(--ink)}
.points{left:14px;top:410px;list-style:none;font-size:9px;color:var(--navy)}
.points li{height:23px;display:flex;align-items:center;gap:8px}
.points li::before{content:"";width:5px;height:5px;border-radius:50%;background:var(--navy)}
.ghost-btn{left:14px;top:516px;width:138px;height:34px;border-radius:17px;background:var(--soft);font-size:8.5px;font-weight:500;color:var(--ink);display:flex;align-items:center;padding-left:16px;gap:10px}
.t-card{top:364px;width:102px;height:187px;border-radius:10px;background:var(--soft);text-align:center;padding:0 8px}
.t-card.navy{background:var(--navy);color:#fff}
.t-card.orange{background:var(--orange);color:#fff}
.avatar{width:40px;height:40px;border-radius:50%;margin:45px auto 0;background:linear-gradient(160deg,#8c7b70,#3a3230)}
.avatar.mark{background:#fff;display:flex;align-items:center;justify-content:center}
.t-name{margin-top:14px;font-size:7.5px;font-weight:600}
.t-text{margin-top:16px;font-size:7px;line-height:10px}

/* insight grid */
.i-card{width:208px;height:136px;border:1px solid var(--line);border-radius:10px;background:var(--card);padding:14px 12px 0 12px;display:flex;gap:10px}
.i-icon{flex:none;width:22px;height:22px;border-radius:50%;background:var(--soft)}
.i-title{font-size:14px;line-height:16.5px;font-weight:400;color:var(--blue);letter-spacing:-.2px}
.i-tag{margin-top:7px;font-size:7.5px;color:var(--blue)}
.i-copy{margin-top:7px;font-size:6.5px;line-height:9px;color:var(--text)}
.rating{margin-top:10px;display:flex;align-items:center;gap:2px;font-size:6px;color:var(--muted)}
.rating svg{width:10px;height:10px}
.rating span{margin-left:4px}

/* contact */
.c-kicker{left:456px;top:631px;font-size:19px;font-weight:600;color:var(--ink)}
.c-title{left:456px;top:662px;font-size:21px;line-height:26px;font-weight:600;color:var(--ink);letter-spacing:-.3px}
.c-sub{left:456px;top:752px;font-size:9px;color:var(--blue)}
.field{left:456px;width:202px;height:31px;border:1px solid var(--line);border-radius:16px;font-size:8px;color:var(--ink);display:flex;align-items:center;padding-left:12px}
.c-area{left:456px;top:990px;width:202px;height:101px;border-radius:10px;background:var(--soft);padding:32px 10px 0;font-size:7.5px;line-height:11px;color:var(--ink)}
.c-btn{left:456px;top:1108px;width:202px;height:32px;border-radius:16px;background:var(--dark);color:#fff;font-size:8px;font-weight:600;display:flex;align-items:center;justify-content:center;text-transform:uppercase}
.c-link{left:456px;top:1150px;width:202px;text-align:center;font-size:7.5px;font-weight:700;color:var(--ink);text-transform:uppercase}
.c-link em{font-style:normal;color:var(--blue)}
</style>
</head>
<body>
<svg width="0" height="0" style="position:absolute">
  <defs>
    <symbol id="star" viewBox="0 0 20 20"><polygon points="10,1 12.6,7 19,7.4 14,11.6 15.6,18 10,14.5 4.4,18 6,11.6 1,7.4 7.4,7" fill="#f2b84b"/></symbol>
  </defs>
</svg>

<header>
  <div class="abs brand"><span class="brand-dot"></span>Norvale</div>
  <nav class="abs nav"><span>Home</span><span>About</span><span>Method</span><span>Insights</span></nav>
  <div class="abs nav-cta">Book a call</div>
</header>

<section class="hero">
  <div class="abs eyebrow">Learn Resources</div>
  <h1 class="abs hero-title">Norvale &amp;<br>Adaptive 8 Method</h1>
  <p class="abs hero-copy">Calibrate high-stakes ERP programs with an adaptive, structured method that keeps each phase focused on the few decisions that truly matter for a smooth, lasting delivery.</p>
  <div class="abs hero-btn"><span class="ico"></span>Access resources ▾</div>
  <div class="abs video" role="img" aria-label="Video still of a modern glass office tower">
    <div class="abs video-label"><span class="c"></span>Insights</div>
    <svg class="abs video-bar" viewBox="0 0 333 40">
      <rect x="0" y="4" width="14" height="12" rx="3" fill="#fff"/>
      <polygon points="32,5 32,15 40,10" fill="#fff"/>
      <rect x="47" y="5" width="2" height="10" fill="#fff"/>
      <polygon points="300,5 300,15 307,10" fill="#fff"/>
      <circle cx="315" cy="10" r="5" fill="none" stroke="#fff" stroke-width="1.5"/>
      <circle cx="328" cy="10" r="5" fill="none" stroke="#fff" stroke-width="1.5"/>
      <rect x="10" y="28" width="314" height="3" rx="1.5" fill="#fff" opacity=".85"/>
      <circle cx="12" cy="29.5" r="4" fill="#fff"/>
    </svg>
  </div>
</section>

<section class="testimonials">
  <h2 class="abs section-title">Testimonials</h2>
  <ul class="abs points">
    <li>Proven structured delivery</li>
    <li>Focused on critical factors</li>
    <li>Built for CIO teams</li>
    <li>Results that stay on track</li>
  </ul>
  <div class="abs ghost-btn">⌄ Read the resources</div>

  <article class="abs t-card navy" style="left:226px">
    <div class="avatar" role="img" aria-label="Portrait of client"></div>
    <div class="t-name">Rosa Hartwell</div>
    <p class="t-text">Clear guidance on our core rollout, steady focus and real results.</p>
  </article>
  <article class="abs t-card" style="left:336px">
    <div class="avatar" role="img" aria-label="Portrait of client"></div>
    <div class="t-name">Tom Ridley</div>
    <p class="t-text">Less risk, sharper scope and a team that stayed on budget.</p>
  </article>
  <article class="abs t-card" style="left:447px">
    <div class="avatar" role="img" aria-label="Portrait of client"></div>
    <div class="t-name">Cara White</div>
    <p class="t-text">Our finance teams felt ready and aligned at go-live.</p>
  </article>
  <article class="abs t-card orange" style="left:559px">
    <div class="avatar mark"><svg width="18" height="18" viewBox="0 0 18 18"><rect x="3" y="6" width="12" height="9" rx="1.5" fill="none" stroke="#1f4365" stroke-width="1.6"/><path d="M6 6V4h6v2" fill="none" stroke="#1f4365" stroke-width="1.6"/></svg></div>
    <div class="t-name">Our Commitment</div>
    <p class="t-text">Lasting change across every project and every stakeholder group.</p>
  </article>
</section>

<section class="insights">
  <article class="abs i-card" style="left:14px;top:610px"><span class="i-icon"></span><div>
    <h3 class="i-title">Why early scope drives lasting delivery</h3>
    <div class="i-tag">Project planning</div>
    <p class="i-copy">Define priorities before vendors and keep the core team aligned on goals.</p>
    <div class="rating"><svg><use href="#star"/></svg><svg><use href="#star"/></svg><svg><use href="#star"/></svg><svg><use href="#star"/></svg><span>5.0 rating</span></div></div></article>
  <article class="abs i-card" style="left:233px;top:610px"><span class="i-icon"></span><div>
    <h3 class="i-title">Measure progress by checking real readiness</h3>
    <div class="i-tag">Go-live readiness</div>
    <p class="i-copy">Simple checks that reveal gaps in data, training and process design.</p>
    <div class="rating"><svg><use href="#star"/></svg><svg><use href="#star"/></svg><svg><use href="#star"/></svg><svg><use href="#star"/></svg><span>4.8 rating</span></div></div></article>
  <article class="abs i-card" style="left:14px;top:756px"><span class="i-icon"></span><div>
    <h3 class="i-title">Make leadership clearly own the goals</h3>
    <div class="i-tag">Governance</div>
    <p class="i-copy">Executive roles that keep decisions quick and accountable.</p>
    <div class="rating"><svg><use href="#star"/></svg><svg><use href="#star"/></svg><svg><use href="#star"/></svg><svg><use href="#star"/></svg><span>4.9 rating</span></div></div></article>
  <article class="abs i-card" style="left:233px;top:756px"><span class="i-icon"></span><div>
    <h3 class="i-title">Make room for change in your teams</h3>
    <div class="i-tag">People</div>
    <p class="i-copy">Practical change steps that help users adopt new ways.</p>
    <div class="rating"><svg><use href="#star"/></svg><svg><use href="#star"/></svg><svg><use href="#star"/></svg><svg><use href="#star"/></svg><span>4.7 rating</span></div></div></article>
  <article class="abs i-card" style="left:14px;top:902px"><span class="i-icon"></span><div>
    <h3 class="i-title">Manage vendors with clear contracts</h3>
    <div class="i-tag">Vendor selection</div>
    <p class="i-copy">Set terms and milestones that protect your budget and time.</p>
    <div class="rating"><svg><use href="#star"/></svg><svg><use href="#star"/></svg><svg><use href="#star"/></svg><svg><use href="#star"/></svg><span>4.8 rating</span></div></div></article>
  <article class="abs i-card" style="left:233px;top:902px"><span class="i-icon"></span><div>
    <h3 class="i-title">Move data early and test it often</h3>
    <div class="i-tag">Data migration</div>
    <p class="i-copy">Clean records and repeated test loads reduce launch surprises.</p>
    <div class="rating"><svg><use href="#star"/></svg><svg><use href="#star"/></svg><svg><use href="#star"/></svg><svg><use href="#star"/></svg><span>4.9 rating</span></div></div></article>
  <article class="abs i-card" style="left:14px;top:1047px"><span class="i-icon"></span><div>
    <h3 class="i-title">Keep processes simple and steady</h3>
    <div class="i-tag">Process design and optimisation</div>
    <p class="i-copy">Standard flows first, custom work only where it adds value.</p>
    <div class="rating"><svg><use href="#star"/></svg><svg><use href="#star"/></svg><svg><use href="#star"/></svg><svg><use href="#star"/></svg><span>4.8 rating</span></div></div></article>
  <article class="abs i-card" style="left:233px;top:1047px"><span class="i-icon"></span><div>
    <h3 class="i-title">Wrap up each phase with a review</h3>
    <div class="i-tag">Review</div>
    <p class="i-copy">Short retrospectives that carry lessons into the next stage.</p>
    <div class="rating"><svg><use href="#star"/></svg><svg><use href="#star"/></svg><svg><use href="#star"/></svg><svg><use href="#star"/></svg><span>4.9 rating</span></div></div></article>
</section>

<aside class="contact">
  <div class="abs c-kicker">Begin</div>
  <h2 class="abs c-title">Ready to action<br>using your ERP<br>resources?</h2>
  <p class="abs c-sub">Find out what ERP can do for you?</p>
  <div class="abs field" style="top:789px">Adam Daniel</div>
  <div class="abs field" style="top:829px">Email</div>
  <div class="abs field" style="top:869px">Status / Role</div>
  <div class="abs field" style="top:910px">Sector</div>
  <div class="abs field" style="top:950px">Phone</div>
  <div class="abs c-area">Our team will reply within two working days with the next steps.</div>
  <div class="abs c-btn">Access options</div>
  <div class="abs c-link">Read more resources <em>→</em></div>
</aside>
</body>
</html>
```